New Book Cover Design Project for book about Trade Blend

DetWe need a book cover (front, back, spine) for a new book entitled ‘Trade Blend’’ and subtitled “beyond old rules toward real buyer wishes” (inverted commas not to be part of the title and subtitle). The author is Malcolm Ferrisby. The publisher is Tessellane Insights. The finished size of the paperback version will be 5" x 8" (127 x 203.2 mm). There will be paperback, hardback, and e-book versions. The final number of pages is expected to be in the region of 80 pages. Text for the back cover is in an attached document. At the bottom of the back cover should be publisher logo (rectangular) on the left and space for the ISBN bar code on the right. The design should be original and not include any stock images that have been created by someone else or may require obtaining a copyright licence to use. Symbols in common use and not copyrighted are probably ok. There are no required images, photographs or symbols except the publisher logo at the left bottom of the back cover. Spine lettering should be UK/US style with the top of the writing nearest the front cover. The designer is free to be creative using appropriate diagrams, symbols or abstract designs. A copy of the publisher logo is attached. Designers are assured that when evaluating designs absolutely no notice whatsoever is taken of a designer's Pixel Forum ranking or status; We are completely output driven, so what matters is the design, not the ranking or status of the designer. In a similar way, designs are not evaluated as 'good' or 'bad' - the winning design will be chosen after review by a design review panel and is not decided arbitrarily by a single person. All submitted designs should be capable of effective copyright assignment. Designs submitted for consideration should include front cover, spine, and back cover.
Candidate Trade Blend words that can be included in designs, if the designer wishes, include: product, place, promotion, price, consumer, company objectives, participants, physical evidence, process of service assembly, battery life, usability, security, fashion, design, brand, appearance, health, obedience, sustainability, accessibility, value, idea, information operation, beliefs, vectors.

Target Market(s)

Academics, teachers, text book writers, and students concerned with marketing.

Industry/Entity Type

Education

Font styles to use
Serif

Requirements
Must have
• • Author on the front cover and the spine. Templates have been added to the brief for the cover with spine for a 80 page book. There are .indd and .pdf templates that can be used. the .indd and .pdf templates show where the ISBN blocks should go. The other .PDF templates have the ISBN in the wrong place (middle of the lower back cover) but have more information about the meanings of template markings. Bleeds - PLEASE NOTE - the cover printing is not exact - there is minor variation when the printers print the covers. Therefore do not have solid blocks of colour that go to the edges of the spine or spine and cover pages with different blocks of colour - solid blocks of colour may go round the spine folds a little bit! See the templates - they indicate the areas for possible printing imprecision. The ISBN numbers in the template file names are what will be used - perfect is for the paperback and case is for the hardback.
Nice to have
• • It is not necessary to have the subtitle on the spine. The final book size may not be 80 pages, therefore the spine width may change, but not by much. • Use only standard fonts.
Should not have
• • Ideally, stock images should not be used as we cannot control other uses of images created by other sources, thus potentially damaging the book branding. I don't like solid black cover or spine backgrounds.

```html
<!DOCTYPE html>
<html lang="en">
<head>
<meta charset="utf-8">
<title>Trade Blend — Book Cover</title>
<link rel="stylesheet" href="https://fonts.googleapis.com/css2?family=Crimson+Text:wght@400;600&family=Libre+Baskerville&family=Tinos&display=swap">
<style>
  :root {
    --paper: #ffffff;
    --ink: #111111;
    --muted: #6a6a6a;
    --shade: #bdbdbd;
    --shade-soft: #d6d6d6;
    --art-top: #ff8a00;
    --art-mid: #f0541e;
    --art-low: #a8237a;
    --art-base: #7d0f6e;
    --title-top: #9c2f63;
    --title-low: #c3652e;
    --publisher: #15608f;
    --frame: #000000;
  }
  * { margin: 0; padding: 0; box-sizing: border-box; }
  html, body { width: 1200px; height: 830px; overflow: hidden; background: var(--paper); }
  .cover { position: relative; width: 1200px; height: 830px; overflow: hidden; background: var(--paper); color: var(--ink); }

  /* Back cover */
  .back-art { position: absolute; left: 0; top: 360px; width: 350px; height: 470px; border-top-right-radius: 170px 220px; background: linear-gradient(180deg, var(--shade-soft), var(--shade)); }
  .title-block { position: absolute; width: 360px; text-align: center; font-family: "Tinos", serif; font-weight: 400; line-height: 1; }
  .title-block span { position: absolute; left: 0; width: 100%; white-space: nowrap; }
  .back-title { left: 97px; top: 0; }
  .back-title .small { top: 61px; font-size: 30px; }
  .back-title .large { top: 77px; font-size: 86px; }
  .blurb { position: absolute; left: 44px; top: 190px; width: 474px; font-family: "Crimson Text", serif; font-size: 13.4px; line-height: 16.9px; text-align: justify; hyphens: auto; }
  .author-bio { position: absolute; left: 41px; top: 489px; width: 475px; font-family: "Crimson Text", serif; font-weight: 600; font-size: 13.4px; line-height: 16.9px; text-align: justify; }
  .publisher { position: absolute; left: 48px; top: 730px; font-family: "Crimson Text", serif; font-size: 16px; color: var(--publisher); display: flex; align-items: center; gap: 6px; }
  .publisher .mark { width: 10px; height: 10px; background: var(--publisher); }
  .isbn-space { position: absolute; left: 346px; top: 670px; width: 165px; height: 95px; border: 2.5px solid var(--frame); background: var(--paper); }

  /* Spine — reads bottom to top */
  .spine-title { position: absolute; left: 584px; top: 64px; width: 40px; height: 292px; writing-mode: vertical-rl; transform: rotate(180deg); text-align: center; font-family: "Tinos", serif; font-size: 40px; line-height: 40px; white-space: nowrap; }
  .spine-mark { position: absolute; left: 584px; top: 412px; width: 48px; height: 34px; }
  .spine-author { position: absolute; left: 596px; top: 488px; width: 20px; height: 300px; writing-mode: vertical-rl; transform: rotate(180deg); text-align: center; font-family: "Libre Baskerville", serif; font-size: 15px; line-height: 20px; letter-spacing: 6px; color: var(--muted); white-space: nowrap; }

  /* Front cover */
  .subtitle { position: absolute; left: 690px; top: 55px; width: 482px; text-align: center; font-family: "Libre Baskerville", serif; font-size: 11px; letter-spacing: 3.1px; color: var(--muted); white-space: nowrap; }
  .front-art { position: absolute; left: 732px; top: 108px; width: 288px; height: 492px; border-radius: 40px; background: linear-gradient(180deg, var(--art-top) 0%, var(--art-mid) 40%, var(--art-low) 72%, var(--art-base) 100%); }
  .front-title { left: 742px; top: 0; }
  .front-title .small { top: 599px; font-size: 30px; color: var(--title-top); }
  .front-title .large { top: 623px; font-size: 76px; background: linear-gradient(90deg, var(--title-top), var(--title-low)); -webkit-background-clip: text; background-clip: text; color: transparent; }
  .front-author { position: absolute; left: 690px; top: 754px; width: 476px; text-align: center; font-family: "Libre Baskerville", serif; font-size: 28px; line-height: 1; letter-spacing: 8px; color: var(--muted); white-space: nowrap; }
</style>
</head>
<body>
<main class="cover">

  <!-- Back cover -->
  <div class="back-art" role="img" aria-label="Faint grey painted light bulb decoration"></div>

  <h2 class="title-block back-title"><span class="small">TRADE</span><span class="large">BLEND</span></h2>

  <p class="blurb">This book has been inspired by the many textbooks, classes and student work about trade blend, which simply present or teach trade blend as 4Ps - very often not even acknowledging where those 4Ps came from. This approach is simply unacceptable academic work - no discussion of the extensive research from the 1920s onwards, about what is needed for effective marketing and trade blend. In several ways, this is a thoroughly radical book pushing against the common approach of simply teaching about simplistic 4Ps. Many students produce a trade blend for a company; they shouldn't. The book provides a solid example of what academics often call 'critical thinking'. Other ways in which the book is radical, is that it shows that trade blend is not only for products and services; it is also for ideas. The book discusses the idea that marketing can be seen as a branch of information warfare. Positioning should be included in trade blend considerations. Trade blend should not only be considered for legitimate products, services, and ideas; it is relevant also for those who trade in legal or mixed legal and illegal products and services. Examples are explored in the book.</p>

  <p class="author-bio">Malcolm Ferrisby has extensive experience in industry, academia, and a variety of NGOs working in human and civil rights. Within those contexts, he has a lot of marketing experience as practitioner, academic, and external examiner – contributing to the radical nature of this book.</p>

  <div class="publisher"><span class="mark"></span>Tessellane Insights</div>
  <div class="isbn-space"></div>

  <!-- Spine -->
  <div class="spine-title">TRADE BLEND</div>
  <svg class="spine-mark" viewBox="0 0 48 34" role="img" aria-label="Small dark light bulb motif">
    <ellipse cx="22" cy="17" rx="20" ry="15" fill="var(--ink)"/>
  </svg>
  <div class="spine-author">MALCOLM FERRISBY</div>

  <!-- Front cover -->
  <div class="subtitle">BEYOND OLD RULES TOWARD REAL BUYER WISHES</div>

  <div class="front-art" role="img" aria-label="Painted light bulb in orange to purple with a glowing white filament"></div>

  <h1 class="title-block front-title"><span class="small">TRADE</span><span class="large">BLEND</span></h1>

  <div class="front-author">MALCOLM FERRISBY</div>

</main>
</body>
</html>
```